Agriculture Business Card

I want to use my existing logo and use my tagline of "Don't Guess...Soil Test" on the card. Looking for a double sided card that will really get peoples attention.
Contact Info:
Marlow Field Crop Edge
Calvin Brusk
2917 K Lane
Larkin, NE 68593
402-555-0193
calvin.r.brusk@fieldmailbox.net

```html
<!DOCTYPE html>
<html lang="en">
<head>
<meta charset="utf-8">
<title>Marlow Field Crop Edge – Business Card</title>
<link rel="stylesheet" href="https://fonts.googleapis.com/css2?family=Arimo:wght@400;700&display=swap">
<style>
  :root {
    --page: #2b2e33;
    --card: #1f1f1f;
    --amber: #f4b41a;
    --leaf: #3aa63a;
    --clay: #9a6a50;
    --white: #ffffff;
  }
  * { box-sizing: border-box; margin: 0; padding: 0; }
  html, body {
    width: 1200px; height: 900px; overflow: hidden;
    background: var(--page);
    font-family: "Arimo", Arial, sans-serif;
  }
  .sheet {
    width: 1200px; height: 900px;
    display: flex; justify-content: center; align-items: center; gap: 100px;
  }
  .card {
    width: 400px; height: 700px;
    background: var(--card);
    position: relative;
    box-shadow: 0 18px 40px rgba(0,0,0,.45);
  }
  .card-front .frame {
    position: absolute; inset: 22px;
    border: 2px solid var(--leaf);
  }
  .brand {
    position: absolute; left: 0; right: 0;
    display: flex; flex-direction: column; align-items: center; gap: 16px;
    text-align: center;
  }
  .brand-mark { border-radius: 50%; }
  .brand-name { font-weight: 700; line-height: 1.1; }

  .card-front .brand { top: 100px; }
  .card-front .brand-mark { width: 140px; height: 140px; background: var(--amber); }
  .card-front .brand-name { color: var(--amber); font-size: 24px; width: 300px; }

  .person {
    position: absolute; top: 345px; left: 0; right: 0; text-align: center;
  }
  .person-name {
    color: var(--amber); font-weight: 700; font-size: 34px; letter-spacing: .5px;
  }
  .person-role {
    color: var(--white); font-size: 17px; margin-top: 4px;
  }
  .contact-icons {
    display: flex; justify-content: center; gap: 10px; margin-top: 22px;
  }
  .contact-icons svg { width: 30px; height: 30px; }
  .contact-lines {
    list-style: none; margin-top: 22px;
    color: var(--white); font-size: 17px; line-height: 1.75;
  }

  .card-back .brand { top: 120px; }
  .card-back .brand-mark { width: 190px; height: 190px; background: var(--amber); }
  .card-back .brand-name { color: var(--clay); font-size: 44px; width: 320px; }
  .tagline {
    position: absolute; bottom: 120px; left: 0; right: 0; text-align: center;
    color: var(--white); font-size: 26px;
  }
</style>
</head>
<body>
<main class="sheet">
  <section class="card card-front">
    <div class="frame"></div>
    <div class="brand">
      <span class="brand-mark"></span>
      <span class="brand-name">Marlow Field Crop Edge</span>
    </div>
    <div class="person">
      <h1 class="person-name">CALVIN BRUSK</h1>
      <p class="person-role">CEO/Founder</p>
      <div class="contact-icons">
        <svg viewBox="0 0 30 30" aria-label="phone">
          <circle cx="15" cy="15" r="13" fill="none" stroke="#f4b41a" stroke-width="2"/>
          <path d="M10 9c1-1 2-1 3 1l1 2c0 1-1 1-1 2 1 2 2 3 4 4 1 0 1-1 2-1l2 1c2 1 2 2 1 3-2 2-5 1-8-2s-5-6-4-10z" fill="#f4b41a"/>
        </svg>
        <svg viewBox="0 0 30 30" aria-label="email">
          <circle cx="15" cy="15" r="13" fill="none" stroke="#f4b41a" stroke-width="2"/>
          <rect x="8" y="10" width="14" height="10" rx="1" fill="#f4b41a"/>
          <path d="M8 11l7 5 7-5" fill="none" stroke="#1f1f1f" stroke-width="1.5"/>
        </svg>
        <svg viewBox="0 0 30 30" aria-label="address">
          <circle cx="15" cy="15" r="13" fill="none" stroke="#f4b41a" stroke-width="2"/>
          <path d="M15 7a5 5 0 0 1 5 5c0 4-5 10-5 10s-5-6-5-10a5 5 0 0 1 5-5z" fill="#f4b41a"/>
          <circle cx="15" cy="12" r="2" fill="#1f1f1f"/>
        </svg>
      </div>
      <ul class="contact-lines">
        <li>402-555-0193</li>
        <li>calvin.r.brusk@fieldmailbox.net</li>
        <li>2917 K Lane Larkin, NE 68593</li>
      </ul>
    </div>
  </section>

  <section class="card card-back">
    <div class="brand">
      <span class="brand-mark"></span>
      <span class="brand-name">Marlow Field Crop Edge</span>
    </div>
    <p class="tagline">Don't Guess...Soil Test</p>
  </section>
</main>
</body>
</html>
```